Kestrel Finish Studio (KFS)

I would like to design a dedicated site for my KFS product, which allows industry employees to be trained in the visual inspection of mechanical parts. My product is a 3D simulator (see https://morvint-works.ch/our-applications/virtual-reality/ and https://morvint-works.ch for videos) which makes it possible to manufacture standard parts representative of a type of defect which is accepted or refused by the quality department. These master parts can be used to create a common quality culture in the company and to train employees in a homogeneous way. The simulator is initially designed for watchmaking, but must be designed for much broader industries (cars, phone reconditioning, ball bearings, etc.)
L'information que j'ai donnée n'est pas assez précise. Je dois préciser les domaines métiers visés par le site internet. J'ai besoin de quelques jours pour choisir les domaines les plus représentatifs.
Coded - Design and coding required
1 page

```html
<!DOCTYPE html>
<html lang="en">
<head>
<meta charset="utf-8">
<title>Kestrel Finish Studio</title>
<link href="https://fonts.googleapis.com/css2?family=Montserrat:wght@600;700;800&family=Roboto:wght@300;400;500&display=swap" rel="stylesheet">
<style>
:root{
  --blue:#0a74c4;
  --blue-deep:#0a5fa8;
  --navy:#1c1f2b;
  --ink:#1f2230;
  --text:#555a66;
  --white:#ffffff;
  --rule:#e3e5ea;
}
*{margin:0;padding:0;box-sizing:border-box}
html,body{width:1200px;height:3538px;overflow:hidden;background:var(--white)}
body{position:relative;font-family:'Roboto',sans-serif;color:var(--text)}
.abs{position:absolute}
h1,h2,h3,.brand{font-family:'Montserrat',sans-serif;font-weight:700}

/* hero */
.hero{left:0;top:0;width:1200px;height:753px;overflow:hidden}
.hero-photo{left:0;top:0;width:1200px;height:753px;background:radial-gradient(ellipse at 55% 55%,#6b6a66 0%,#3a3a3a 40%,#1a1a1b 80%)}
.hero-shape{left:0;top:0}
.brand{color:var(--white);font-size:22px;line-height:30px;letter-spacing:.3px;text-transform:uppercase}
.nav{top:49px;left:536px;display:flex;gap:0;font-size:13px;font-weight:500;color:var(--white)}
.nav a{color:var(--white);text-decoration:none;position:absolute;white-space:nowrap}
.nav a.active{border-bottom:2px solid var(--white);padding-bottom:4px}
.login{left:1030px;top:49px;font-size:13px;font-weight:500;color:var(--white);display:flex;align-items:center;gap:4px}
.hero-box{left:85px;top:263px;width:523px;height:207px;background:rgba(10,10,12,.62);padding:20px 25px}
.hero-box h1{color:var(--white);font-size:45px;line-height:52px;text-transform:uppercase}
.hero-box p{color:var(--white);font-family:'Montserrat',sans-serif;font-weight:700;font-size:14.5px;line-height:26px;margin-top:12px;text-transform:uppercase}

.section-title{width:1200px;left:0;text-align:center;color:var(--ink);font-size:38px;line-height:43px;text-transform:uppercase}
.pointer{width:0;height:0;border-left:12px solid transparent;border-right:12px solid transparent;border-top:22px solid var(--blue)}
.pointer.white{border-top-color:var(--white)}

/* control */
.checks{left:110px;top:940px;width:480px;list-style:none}
.checks li{position:relative;padding-left:27px;font-size:14px;line-height:21px;margin-bottom:22px;font-weight:300;color:#4a4f5a}
.checks li::before{content:"";position:absolute;left:0;top:4px;border-top:7px solid transparent;border-bottom:7px solid transparent;border-left:14px solid var(--blue)}
.btn{left:111px;top:1203px;width:145px;height:43px;background:var(--blue);color:var(--white);font-size:14px;font-weight:500;display:flex;align-items:center;justify-content:center;text-transform:uppercase}
.accent{background:var(--blue)}
.photo-lab{left:618px;top:947px;width:454px;height:296px;background:linear-gradient(120deg,#4e3040 0%,#7a6a78 40%,#b9b0b4 60%,#3e2a2e 100%)}

/* bands */
.band-bg{left:0}
.band-text{left:0;width:1200px;text-align:center;color:var(--white)}
.band-text h2{font-size:38px;line-height:43px;text-transform:uppercase}
.band-text p{width:810px;margin:0 auto;font-size:15px;line-height:26px;font-weight:300}

/* after sales */
.ui-panel{left:138px;top:2183px;width:120px;height:295px;background:#0e2a4a}
.ring-view{left:262px;top:2183px;width:331px;height:295px;background:radial-gradient(ellipse at 55% 45%,#7a5318 0%,#3a2606 35%,#050505 70%)}
.body-copy{font-size:14px;line-height:26px;font-weight:300;color:#4a4f5a;text-align:justify}

/* footer */
.foot-head{font-family:'Montserrat',sans-serif;font-weight:700;font-size:13px;color:var(--ink);text-transform:uppercase}
.foot-brand{color:var(--ink)}
.foot-links{list-style:none;font-size:12.5px;line-height:34px;color:#4a4f5a}
.contact-row{left:424px;display:flex;gap:12px;font-size:12.5px;line-height:17px;color:#4a4f5a}
.contact-row .ico{width:26px;height:26px;border-radius:50%;background:var(--navy);flex:none;display:flex;align-items:center;justify-content:center}
.rule{left:98px;top:3448px;width:1002px;height:1px;background:var(--rule)}
.copy{left:0;top:3490px;width:1200px;text-align:center;font-size:12px;color:#4a4f5a}
</style>
</head>
<body>

<!-- Hero -->
<section class="abs hero">
  <div class="abs hero-photo" role="img" aria-label="Watchmaker's hands assembling a mechanical movement with tweezers among gears and parts"></div>
  <svg class="abs hero-shape" width="1200" height="753" viewBox="0 0 1200 753">
    <polygon points="640,692 1200,625 1200,753" fill="#0a74c4"/>
    <polygon points="0,753 560,690 600,652 640,692 1200,753" fill="#ffffff"/>
    <polyline points="592,686 600,694 608,686" fill="none" stroke="#1f2230" stroke-width="2"/>
    <polyline points="592,679 600,687 608,679" fill="none" stroke="#1f2230" stroke-width="2"/>
  </svg>
  <div class="abs brand" style="left:110px;top:28px">Kestrel Finish<br>Studio</div>
  <nav class="abs nav">
    <a class="active" style="left:0">HOME</a>
    <a style="left:74px">ABOUT US</a>
    <a style="left:176px">SERVICES</a>
    <a style="left:275px">BLOG</a>
    <a style="left:344px">CONTACT US</a>
  </nav>
  <div class="abs login">
    <svg width="12" height="12" viewBox="0 0 12 12"><circle cx="6" cy="3.5" r="3" fill="#fff"/><path d="M0 12 C0 7 12 7 12 12Z" fill="#fff"/></svg>LOGIN
  </div>
  <div class="abs hero-box">
    <h1>Kestrel Finish<br>Studio</h1>
    <p>Virtual reality at the service of controlled<br>aesthetic watchmaking</p>
  </div>
</section>

<!-- How to control it -->
<h2 class="abs section-title" style="top:816px">How to control it?</h2>
<div class="abs pointer" style="left:586px;top:878px"></div>
<ul class="abs checks">
  <li>Adopting a simple and unambiguous language for a common understanding of aesthetic quality at the extended enterprise level.</li>
  <li>By using a semantic reference matrix associating the types of anomalies (scratches, marks, deformations, stains, etc.) with the intensity levels defined with the company.</li>
  <li>Determining the compliance thresholds of the component or product.</li>
  <li>Providing uniform training in operational competence for those responsible for aesthetic control.</li>
</ul>
<div class="abs btn">Learn more</div>
<div class="abs accent" style="left:950px;top:1137px;width:137px;height:121px"></div>
<div class="abs photo-lab" role="img" aria-label="Technician inspecting a small part under a measuring instrument with a monitor"></div>

<!-- Lighten band -->
<svg class="abs band-bg" style="top:1362px" width="1200" height="625" viewBox="0 0 1200 625">
  <rect width="1200" height="625" fill="#1c1f2b"/>
  <polygon points="0,128 1200,0 1200,496 0,625" fill="#0a74c4"/>
  <polygon points="560,64 1200,0 1200,496 560,563" fill="#0b6cb8" opacity=".6"/>
</svg>
<div class="abs band-text" style="top:1528px">
  <h2>Lighten the management of<br>physical components</h2>
  <div class="pointer white" style="margin:12px auto 18px"></div>
  <p>Companies must manage and maintain sets of physical components used as a "yardstick" for the training of aesthetic testers. The cost of managing a set of physical parts representing all combinations of shapes, defect types, materials and finishes is very high.</p>
  <p style="margin-top:26px">KFS allows the company to significantly reduce its management burden by scanning components or products in 3D and then virtually adding 'typical' aesthetic anomalies.</p>
</div>

<!-- After-sales -->
<h2 class="abs section-title" style="top:2034px">Improve after-sales<br>service returns</h2>
<div class="abs pointer" style="left:586px;top:2130px"></div>
<div class="abs accent" style="left:124px;top:2375px;width:136px;height:119px"></div>
<div class="abs ui-panel" role="img" aria-label="Simulator settings panel with defect sliders and toggles"></div>
<div class="abs ring-view" role="img" aria-label="3D render of a golden watch case ring on a black background"></div>
<div class="abs body-copy" style="left:630px;top:2175px;width:446px">
  <p>The KFS platform can easily be used by the service network staff to assist them in the objective assessment of aesthetic defects by referring to the semantic matrix as well as to the cases already referenced.</p>
  <p style="margin-top:26px">It is also possible, in an intuitive and playful way, to indicate, in accordance with the product nomenclature, a type of imperfection, its intensity and its location. It is also possible to draw up a precise repair estimate or to declare a non-conformity on a product coming from a market return.</p>
</div>

<!-- Studio band -->
<svg class="abs band-bg" style="top:2595px" width="1200" height="570" viewBox="0 0 1200 570">
  <rect width="1200" height="570" fill="#1c1f2b"/>
  <polygon points="0,0 600,68 1200,0 1200,570 0,440" fill="#0a74c4"/>
  <polygon points="600,68 1200,0 1200,130" fill="#1c1f2b"/>
  <polygon points="600,68 1200,130 1200,570 700,515" fill="#0e80d4" opacity=".5"/>
</svg>
<div class="abs body-copy" style="left:110px;top:2758px;width:475px;color:#fff;font-weight:300">
  Morvint Works Lab a développé en collaboration avec l'école d'horlogerie de Valmont un simulateur de défaut sur pièce mécanique. Celui-ci permet aux enseignants de former les élèves de manière plus approfondie au métier de contrôleur qualité. Cet outil combiné avec un LMS (Learning Management System) ou l'interface de gestion intégrée permet d'animer une formation de contrôle esthétique de manière ludique et efficace. Voilà la brochure du produit en attendant le site dédié.
</div>
<h2 class="abs" style="left:600px;top:2840px;width:488px;text-align:right;color:#fff;font-size:38px;line-height:43px;text-transform:uppercase">Kestrel Finish<br>Studio</h2>
<div class="abs pointer white" style="left:1065px;top:2934px"></div>

<!-- Footer -->
<footer>
  <div class="abs brand foot-brand" style="left:110px;top:3215px">Kestrel Finish<br>Studio</div>
  <p class="abs body-copy" style="left:110px;top:3290px;width:235px;font-size:12.5px;line-height:21.5px">Lorem ipsum dolor sit amet, consecte tur adipiscing elit, sed do eiusmod tempor incididunt ut labore et dolore magna aliqua. Ut enim ad minim veniam,quis nostrud</p>

  <div class="abs foot-head" style="left:424px;top:3214px">Contact us</div>
  <div class="abs contact-row" style="top:3256px">
    <span class="ico"><svg width="12" height="14" viewBox="0 0 12 14"><path d="M6 0C2.7 0 0 2.5 0 5.6 0 9.5 6 14 6 14s6-4.5 6-8.4C12 2.5 9.3 0 6 0z" fill="#fff"/><circle cx="6" cy="5.5" r="2" fill="#1c1f2b"/></svg></span>
    <span>123, Lorem ipsum dolor sit<br>consectetur adipiscing</span>
  </div>
  <div class="abs contact-row" style="top:3311px">
    <span class="ico"><svg width="12" height="12" viewBox="0 0 12 12"><path d="M2.5 0.5l2 2.5-1.2 1.5c.8 1.7 2.2 3.1 3.9 3.9L8.7 7.2l2.8 2-1 2.3C5 11.5.5 7 .5 1.5z" fill="#fff"/></svg></span>
    <span>Call Us<br>+41 79 555 01 23</span>
  </div>
  <div class="abs contact-row" style="top:3366px">
    <span class="ico"><svg width="12" height="9" viewBox="0 0 12 9"><rect width="12" height="9" rx="1" fill="#fff"/><polyline points="0.5,0.8 6,5 11.5,0.8" fill="none" stroke="#1c1f2b" stroke-width="1.2"/></svg></span>
    <span>E mail Us<br>info@kestrelfinish.ch</span>
  </div>

  <div class="abs foot-head" style="left:767px;top:3214px">Menu</div>
  <ul class="abs foot-links" style="left:767px;top:3240px">
    <li>Home</li><li>About Us</li><li>Services</li><li>Reviews</li><li>Contact Us</li>
  </ul>
  <div class="abs foot-head" style="left:937px;top:3214px">Support</div>
  <ul class="abs foot-links" style="left:937px;top:3240px">
    <li>Privacy policy</li><li>Terms &amp; Condition</li><li>Faq</li><li>Contact us</li><li>Support</li>
  </ul>

  <div class="abs rule"></div>
  <div class="abs copy">Copyright © 2023 All Rights Reserved</div>
</footer>

</body>
</html>
```